Design a web site for my business - Brightline Coatings Co.

We are a family business that handles design, fabrication and installation of powder coated aluminum, stainless steel and glass products. Including handrails, privacy slat screens, electric gates and pool fencing. We are based in the Whitsundays in North Queensland and service an area from Airlie Beach to Townsville.

Target Market(s)

Domestic and commercial

Industry/Entity Type

fabrication - manufacturing

Coding

Coded - Design and coding required

Number of Pages Required

5+ page

Colors
0054AA
0677BA
7BADD7
CADEEF
E8F1F8

Requirements
Must have
• photo galleries, contact page, one page for privacy screens, balustrades, glass fencing, stainless steel handrail, powder coated aluminium handrails and pool fencing

```html
<!DOCTYPE html>
<html lang="en">
<head>
<meta charset="utf-8">
<title>Brightline Coatings Co — Mobile Screens</title>
<link href="https://fonts.googleapis.com/css2?family=Inter:wght@400;500;600;700;800&display=swap" rel="stylesheet">
<style>
:root{
  --brand:#0054AA;
  --brand-2:#0677BA;
  --brand-3:#7BADD7;
  --brand-4:#CADEEF;
  --brand-5:#E8F1F8;
  --deep:#062a55;
  --deep-2:#0a3466;
  --ink:#0b1a2e;
  --paper:#f7f9fc;
  --panel:#eef4fa;
  --line:#d3e1ee;
  --text:#22303f;
  --muted:#566574;
  --soft:#8796a6;
  --white:#ffffff;
}
*{box-sizing:border-box;margin:0;padding:0}
html,body{width:1200px;height:3262px;overflow:hidden;background:var(--white)}
body{font-family:'Inter',sans-serif;color:var(--text);position:relative}
a{color:inherit;text-decoration:none}
.screen{position:absolute;top:44px;width:258px;background:var(--paper);overflow:hidden}
.a{position:absolute}
.hdr{position:absolute;left:0;top:0;width:100%;height:51px;display:flex;align-items:center;justify-content:space-between;padding:0 11px;background:var(--paper);border-bottom:1px solid var(--brand-5)}
.logo{display:flex;align-items:center;gap:4px;font-size:6px;font-weight:700;color:var(--brand);line-height:1.1;width:60px}
.logo i{display:block;width:10px;height:10px;background:var(--brand);border-radius:50%;flex:none}
.btn-dark{background:var(--brand);color:#fff;font-size:9px;font-weight:600;padding:9px 11px;border-radius:2px}
.btn-dark.sm{font-size:8px;padding:9px 15px}
h1,h2,h3{color:var(--ink);font-weight:700;letter-spacing:-.01em}
.eyebrow{font-size:7.5px;font-weight:700;letter-spacing:.08em;text-transform:uppercase;color:var(--brand)}
.p{font-size:10.5px;line-height:1.55;color:var(--muted)}
.bnav{position:absolute;left:0;width:100%;height:36px;background:#fff;display:flex;justify-content:space-around;align-items:center;border-top:1px solid var(--line)}
.bnav a{display:flex;flex-direction:column;align-items:center;gap:2px;font-size:6px;color:var(--soft);text-transform:uppercase;letter-spacing:.04em}
.bnav a.on{color:var(--brand);font-weight:700}
.bnav svg{width:11px;height:11px}
.hero-title{font-size:21px;line-height:1.25;color:#fff;text-align:center;font-weight:700}
.hero-sub{font-size:10.5px;line-height:1.5;color:#f1f5fa;text-align:center}
.btn-white{background:#fff;color:var(--brand);font-size:8px;font-weight:600;text-align:center;border-radius:2px;height:31px;line-height:31px}
.btn-ghost{border:1.5px solid #fff;color:#fff;font-size:8px;font-weight:600;text-align:center;height:32px;line-height:29px}
.stats{background:var(--brand);display:flex;justify-content:space-around;align-items:center;color:#fff;text-align:center}
.stats b{display:block;font-size:21px;font-weight:700}
.stats small{font-size:7px;color:var(--brand-4)}
.svc{left:11px;width:236px;overflow:hidden;display:block}
.svc .txt{position:absolute;left:21px;right:21px;bottom:22px;color:#fff}
.svc h3{color:#fff;font-size:15px;font-weight:600;line-height:1.25;margin-bottom:5px}
.svc p{font-size:9.5px;line-height:1.5;color:#dde8f3}
.svc .cta{margin-top:12px;border:1px solid #fff;height:28px;line-height:26px;text-align:center;font-size:8px;font-weight:600}
.quote{background:var(--brand-5);text-align:center;padding:0 12px}
.quote .q{font-size:13px;line-height:1.52;color:var(--text)}
.label{font-size:7px;font-weight:700;letter-spacing:.07em;text-transform:uppercase;color:var(--ink);margin-bottom:8px}
.field{border:1px solid var(--line);background:#fff;height:31px;font-size:10px;color:#8796a6;padding:0 8px;display:flex;align-items:center;justify-content:space-between;margin-bottom:16px}
.field.grey{background:var(--panel)}
.foot{background:var(--deep);color:#fff;padding:0 11px}
.foot h2{color:#fff;font-size:16px;font-weight:700}
.foot .t{font-size:10px;line-height:1.55;color:var(--brand-4)}
.foot .hd{font-size:7px;font-weight:700;letter-spacing:.08em;color:var(--brand-3);text-transform:uppercase;margin:22px 0 10px}
.foot ul{list-style:none}
.foot li{font-size:10.5px;line-height:1;margin-bottom:11px;color:#eef4fa}
.foot li.dim{color:var(--brand-3)}
.pills{display:flex;gap:7px}
.pill{font-size:7.5px;font-weight:600;padding:6px 16px;border-radius:20px;background:var(--brand-5);color:var(--muted);white-space:nowrap}
.pill.on{background:var(--brand);color:#fff}
.gcard{left:10px;width:236px;background:#fff;border:1px solid var(--line);overflow:hidden;display:block}
.gcard .img{height:177px;position:relative}
.tag{position:absolute;left:10px;top:10px;background:var(--brand);color:#fff;font-size:7px;font-weight:600;padding:3px 6px}
.gcard .body{padding:14px 16px;position:relative}
.gcard h3{font-size:14px;line-height:1.3;font-weight:600;margin-bottom:9px;padding-right:22px}
.gcard .p{font-size:9.5px;line-height:1.6}
.gcard .arr{position:absolute;right:16px;top:14px;width:10px;height:10px}
.loc{display:flex;align-items:center;gap:5px;font-size:8.5px;color:var(--muted);margin-top:10px}
.loc svg{width:9px;height:9px}
.btn-outline{border:1.5px solid var(--brand);background:#fff;text-align:center;font-size:10px;font-weight:600;color:var(--brand)}
.xcard{left:10px;width:236px;background:var(--panel);border:1px solid var(--line);padding:16px}
.xcard .img{height:168px;margin-bottom:14px}
.xcard h3{font-size:15px;font-weight:600;display:flex;align-items:center;gap:6px;margin-bottom:10px}
.xcard h3 svg{width:12px;height:12px}
.xcard .p{font-size:9.5px;line-height:1.62}
.more{display:flex;align-items:center;gap:5px;font-size:9.5px;font-weight:700;color:var(--brand);margin-top:10px}
.more svg{width:10px;height:10px}
.badge{background:var(--brand);color:#fff;font-size:7px;font-weight:600;letter-spacing:.06em;padding:3px 7px}
.standard{background:var(--brand);color:#fff;text-align:center}
.standard h2{color:#fff;font-size:21px;line-height:1.3}
.checks{display:flex;flex-direction:column;align-items:center;gap:20px;font-size:7.5px;font-weight:600}
.checks span{display:flex;align-items:center;gap:6px}
.checks svg{width:13px;height:13px}
.box{left:10px;width:236px;background:var(--panel);border:1px solid var(--line)}
.box.white{background:#fff}
.box h3{font-size:16px;font-weight:600;margin:8px 0 8px}
.chip{display:inline-block;font-size:8.5px;color:var(--brand);background:var(--brand-4);padding:5px 8px;margin:0 5px 6px 0}
.icon{width:16px;height:16px}
.dash{border:1.5px dashed var(--brand-3);height:90px;display:flex;flex-direction:column;align-items:center;justify-content:center;gap:6px;font-size:8.5px;line-height:1.4;color:var(--muted);text-align:center;background:var(--brand-5)}
</style>
</head>
<body>

<!-- ========== HOME ========== -->
<section class="screen" style="left:53px;height:3164px">
  <header class="hdr"><a class="logo" href="index.html"><i></i>Brightline Coatings Co</a><a class="btn-dark" href="contact.html">Request Quote</a></header>

  <div class="a" style="left:0;top:51px;width:258px;height:488px;background:linear-gradient(180deg,#8fa6c0 0%,#6f8596 30%,#3f5a58 55%,#3a4048 72%,#8a5a2c 88%,#3a2a1d 100%)" role="img" aria-label="Coastal waterfront home with timber and glass balustrade overlooking the sea"></div>
  <div class="a" style="left:0;top:51px;width:258px;height:488px;background:rgba(0,84,170,.22)"></div>
  <h1 class="a hero-title" style="left:14px;top:162px;width:230px">Precision Fabrication for the Queensland Coast</h1>
  <p class="a hero-sub" style="left:10px;top:254px;width:238px">Architectural aluminum and steel solutions designed to withstand the harsh marine environment of the Whitsundays.</p>
  <a class="a btn-white" style="left:11px;top:332px;width:236px" href="gallery.html">View Our Work</a>
  <a class="a btn-ghost" style="left:11px;top:375px;width:236px" href="process.html">Our Process</a>

  <nav class="bnav" style="top:539px">
    <a class="on" href="index.html"><svg viewBox="0 0 12 12" fill="none" stroke="currentColor"><path d="M1.5 6 6 2l4.5 4v4.5h-3v-3h-3v3h-3z"/></svg>Home</a>
    <a href="services.html"><svg viewBox="0 0 12 12" fill="none" stroke="currentColor"><path d="M2 10 7 5M8 1.5a2.5 2.5 0 0 0 2.5 3L10 5 7 2zM2 2l3 3"/></svg>Services</a>
    <a href="gallery.html"><svg viewBox="0 0 12 12" fill="none" stroke="currentColor"><rect x="1.5" y="2" width="9" height="8"/><path d="m2 9 3-3 2 2 1.5-1.5L10 8"/></svg>Projects</a>
    <a href="contact.html"><svg viewBox="0 0 12 12" fill="none" stroke="currentColor"><rect x="1.5" y="2.5" width="9" height="7"/><path d="m1.5 3 4.5 3.5L10.5 3"/></svg>Contact</a>
  </nav>
  <div class="a stats" style="left:0;top:575px;width:258px;height:95px">
    <div><b>100%</b><small>Corrosion Resistant</small></div>
    <div><b>Local</b><small>Airlie Beach Owned</small></div>
  </div>

  <div class="a eyebrow" style="left:11px;top:734px">Expert Services</div>
  <h2 class="a" style="left:11px;top:752px;font-size:20px;line-height:1.3">Coastal Architectural Solutions</h2>

  <a class="a svc" href="handrails.html" style="top:844px;height:252px;background:linear-gradient(180deg,#8f9aa0,#5b6b6a 45%,#2f3f55 80%,#1f2c44)" role="img" aria-label="Stainless steel and glass handrail beside coastal gardens">
    <div class="txt"><h3>Marine-Grade Handrails</h3><p>Engineered stainless steel and aluminum railing systems for high-salt environments.</p></div>
  </a>
  <a class="a svc" href="pool-fencing.html" style="top:1118px;height:252px;background:linear-gradient(180deg,#4f6a60,#2f4a40 45%,#2f4a5e 70%,#1f2c44)" role="img" aria-label="Frameless glass pool fence surrounded by tropical plants">
    <div class="txt"><h3>Glass &amp; Slatted Fencing</h3><p>Safety meets aesthetic with our custom pool fencing solutions.</p></div>
  </a>
  <a class="a svc" href="privacy-screens.html" style="top:1392px;height:209px;background:linear-gradient(180deg,#0a3466,#0054AA 45%,#3d6a96 75%,#1f3556)" role="img" aria-label="Powder-coated aluminium slat privacy screen at dusk">
    <div class="txt" style="bottom:20px"><h3>Privacy &amp; Decorative Screens</h3><p>Powder-coated aluminum slats providing airflow and privacy without compromising style.</p><div class="cta">View Specification</div></div>
  </a>

  <div class="a quote" style="left:0;top:1665px;width:258px;height:369px">
    <div class="eyebrow" style="margin-top:64px">Client Testimonials</div>
    <p class="q" style="margin-top:20px">"The team at Brightline Coatings Co delivered a stunning glass balustrade for our beachfront renovation. The attention to detail and ability to handle the coastal site challenges was exceptional. Truly the best in the region."</p>
    <div style="width:32px;height:2px;background:var(--brand);margin:28px auto 14px"></div>
    <div style="font-size:10px;font-weight:700;color:var(--ink)">Daniel R.</div>
    <div style="font-size:7px;letter-spacing:.05em;color:var(--muted);margin-top:3px">HAMILTON ISLAND DEVELOPER</div>
  </div>

  <div class="a" style="left:11px;top:2097px;width:236px;height:511px;background:#fff;border:1px solid var(--line);padding:22px 21px">
    <h2 style="font-size:20px;line-height:1.3">Ready to Build Your Coastal Vision?</h2>
    <p class="p" style="margin-top:20px">Get a precise quote for your custom fabrication project today. We service Airlie Beach, Bowen, and Townsville.</p>
    <div style="display:flex;align-items:center;gap:10px;margin-top:22px;font-size:10.5px;font-weight:500;color:var(--ink)"><svg width="12" height="12" viewBox="0 0 12 12" fill="none" stroke="#0054AA"><path d="M2 1.5h2l1 2.5-1.3 1a6 6 0 0 0 3.3 3.3l1-1.3 2.5 1v2A1 1 0 0 1 9.5 11 8.5 8.5 0 0 1 1 2.5a1 1 0 0 1 1-1z"/></svg>07 49XX XXXX</div>
    <div style="display:flex;align-items:center;gap:10px;margin-top:13px;font-size:10.5px;color:var(--muted)"><svg width="12" height="12" viewBox="0 0 12 12" fill="none" stroke="#0054AA"><path d="M6 11s4-3.6 4-6.5a4 4 0 0 0-8 0C2 7.4 6 11 6 11z"/><circle cx="6" cy="4.5" r="1.4"/></svg>Airlie Beach, QLD, 4802</div>
    <div style="margin-top:18px;border:1px solid var(--line);padding:22px 20px 4px;box-shadow:0 2px 6px rgba(0,84,170,.08)">
      <div class="label">Full Name</div><div class="field">John Smith</div>
      <div class="label">Phone Number</div><div class="field">0400 000 000</div>
      <div class="label">Service Required</div><div class="field" style="color:var(--ink)">Handrails / Balustrades</div>
    </div>
  </div>

  <footer class="a foot" style="left:0;top:2672px;width:258px;height:492px;padding-top:38px">
    <h2>Brightline Coatings Co</h2>
    <p class="t" style="margin-top:12px">Precision Craftsmanship for the Coast.</p>
    <div class="hd" style="margin-top:32px">Our Services</div>
    <ul><li class="dim"><a href="handrails.html">Handrails</a></li><li class="dim"><a href="privacy-screens.html">Privacy Screens</a></li><li class="dim"><a href="electric-gates.html">Electric Gates</a></li><li class="dim"><a href="pool-fencing.html">Pool Fencing</a></li><li class="dim"><a href="custom-fabrication.html">Custom Fabrication</a></li></ul>
    <div class="hd">Service Areas</div>
    <ul><li>Airlie Beach</li><li>Bowen</li><li>Townsville</li><li>Whitsunday Islands</li></ul>
    <div class="hd">Legal</div>
    <ul><li>© 2024 Brightline Coatings Co.</li><li><a href="privacy.html">Privacy Policy</a></li></ul>
  </footer>
</section>

<!-- ========== GALLERY ========== -->
<section class="screen" style="left:331px;height:2621px">
  <header class="hdr"><a class="logo" href="index.html"><i></i>Brightline Coatings Co</a><svg width="12" height="10" viewBox="0 0 12 10" stroke="#0054AA" stroke-width="1.4"><path d="M1 1h10M1 5h10M1 9h10"/></svg></header>
  <h1 class="a" style="left:11px;top:74px;font-size:21px">Project Gallery</h1>
  <p class="a p" style="left:11px;top:112px;width:232px">Explore our portfolio of high-precision fabrication and powder coating projects across the Whitsunday region.</p>
  <div class="a pills" style="left:11px;top:187px"><span class="pill on">All Projects</span><span class="pill">Balustrades</span><span class="pill">Pool Fencing</span></div>

  <a class="a gcard" href="glass-balustrades.html" style="top:244px;height:300px">
    <div class="img" style="background:linear-gradient(180deg,#b9c8d6,#4d5560 40%,#2c2f36 70%,#6c7a88)" role="img" aria-label="Coastal residence with glass balustrade decks"><span class="tag">Glass Balustrades</span></div>
    <div class="body"><svg class="arr" viewBox="0 0 10 10" fill="none" stroke="#0054AA"><path d="M2 8 8 2M3 2h5v5"/></svg><h3>Luxury Coastal Residence</h3><p class="p">Precision-engineered glass balustrading and structural steel for a multi-level waterfront home in Airlie Beach.</p></div>
  </a>
  <nav class="bnav" style="top:539px;background:var(--brand-5)">
    <a href="index.html"><svg viewBox="0 0 12 12" fill="none" stroke="currentColor"><path d="M1.5 6 6 2l4.5 4v4.5h-3v-3h-3v3h-3z"/></svg>Home</a>
    <a class="on" href="gallery.html"><svg viewBox="0 0 12 12" fill="currentColor"><rect x="1.5" y="1.5" width="4" height="4"/><rect x="6.5" y="1.5" width="4" height="4"/><rect x="1.5" y="6.5" width="4" height="4"/><rect x="6.5" y="6.5" width="4" height="4"/></svg>Projects</a>
    <a href="services.html"><svg viewBox="0 0 12 12" fill="none" stroke="currentColor"><path d="M2 10 7 5M8 1.5a2.5 2.5 0 0 0 2.5 3L10 5 7 2zM2 2l3 3"/></svg>Services</a>
    <a href="contact.html"><svg viewBox="0 0 12 12" fill="none" stroke="currentColor"><rect x="1.5" y="2.5" width="9" height="7"/><path d="m1.5 3 4.5 3.5L10.5 3"/></svg>Contact</a>
  </nav>

  <a class="a gcard" href="handrails.html" style="top:594px;height:341px">
    <div class="img" style="background:linear-gradient(180deg,#7ba6d4,#8a98a0 40%,#5b4a3a 65%,#c16a2a 85%,#6b4a30)" role="img" aria-label="Boardwalk with powder-coated handrail by the water"><span class="tag">Commercial Handrails</span></div>
    <div class="body"><svg class="arr" viewBox="0 0 10 10" fill="none" stroke="#0054AA"><path d="M2 8 8 2M3 2h5v5"/></svg><h3>Public Boardwalk Project</h3><p class="p">Industrial-grade safety handrails featuring high-durability powder coating to withstand the harsh coastal environment.</p><div class="loc"><svg viewBox="0 0 12 12" fill="none" stroke="#0054AA"><path d="M6 11s4-3.6 4-6.5a4 4 0 0 0-8 0C2 7.4 6 11 6 11z"/><circle cx="6" cy="4.5" r="1.4"/></svg>Bowen foreshore</div></div>
  </a>
  <a class="a gcard" href="privacy-screens.html" style="top:956px;height:326px">
    <div class="img" style="background:linear-gradient(180deg,#0a3466,#3d6a96 35%,#b9bcc0 55%,#d6d6d0 85%,#8f969a)" role="img" aria-label="Off-white aluminium slat gate and fence"><span class="tag">Privacy Screens</span></div>
    <div class="body"><svg class="arr" viewBox="0 0 10 10" fill="none" stroke="#0054AA"><path d="M2 8 8 2M3 2h5v5"/></svg><h3>Modern Estate Gate &amp; Slatting</h3><p class="p">Custom aluminum privacy screens and automated gate systems in a contemporary Off-White finish.</p><div class="loc"><svg viewBox="0 0 12 12" fill="none" stroke="#0054AA"><path d="M6 11s4-3.6 4-6.5a4 4 0 0 0-8 0C2 7.4 6 11 6 11z"/><circle cx="6" cy="4.5" r="1.4"/></svg>Townsville North</div></div>
  </a>
  <a class="a gcard" href="pool-fencing.html" style="top:1305px;height:326px">
    <div class="img" style="background:linear-gradient(180deg,#4a6760,#2d4540 45%,#7d8a90 70%,#3a3f48)" role="img" aria-label="Frameless glass pool barrier with tropical landscaping"><span class="tag">Pool Fencing</span></div>
    <div class="body"><svg class="arr" viewBox="0 0 10 10" fill="none" stroke="#0054AA"><path d="M2 8 8 2M3 2h5v5"/></svg><h3>Infinity Pool Glass Barrier</h3><p class="p">Frameless glass pool fencing integrated with natural stone landscaping for an unobstructed ocean view.</p><div class="loc"><svg viewBox="0 0 12 12" fill="none" stroke="#0054AA"><path d="M6 11s4-3.6 4-6.5a4 4 0 0 0-8 0C2 7.4 6 11 6 11z"/><circle cx="6" cy="4.5" r="1.4"/></svg>Hamilton Island</div></div>
  </a>
  <a class="a gcard" href="stainless-handrails.html" style="top:1653px;height:305px">
    <div class="img" style="background:linear-gradient(180deg,#3f5a4e,#5b6a5a 40%,#7a6552 65%,#4a3f35)" role="img" aria-label="Timber deck walkway with stainless wire balustrade on a hillside"><span class="tag">Custom Fabrication</span></div>
    <div class="body"><svg class="arr" viewBox="0 0 10 10" fill="none" stroke="#0054AA"><path d="M2 8 8 2M3 2h5v5"/></svg><h3>Elevated Decking Frame</h3><p class="p">Architectural stainless steel wire balustrading and custom-fabricated deck structure for a hillside terrain.</p><div class="loc"><svg viewBox="0 0 12 12" fill="none" stroke="#0054AA"><path d="M6 11s4-3.6 4-6.5a4 4 0 0 0-8 0C2 7.4 6 11 6 11z"/><circle cx="6" cy="4.5" r="1.4"/></svg>Cannonvale Estates</div></div>
  </a>
  <a class="a btn-outline" href="gallery.html?page=2" style="left:10px;top:1989px;width:236px;height:38px;line-height:35px">View More Projects</a>

  <footer class="a foot" style="left:0;top:2082px;width:258px;height:539px;padding-top:34px">
    <h2>Brightline Coatings Co</h2>
    <p class="t" style="margin-top:12px">Precision craftsmanship for coastal living. Specializing in high-end balustrading and powder coating.</p>
    <div class="hd">Services</div>
    <ul><li class="dim"><a href="handrails.html">Handrails</a></li><li class="dim"><a href="privacy-screens.html">Privacy Screens</a></li><li class="dim"><a href="electric-gates.html">Electric Gates</a></li><li class="dim"><a href="pool-fencing.html">Pool Fencing</a></li></ul>
    <div class="hd">Location</div>
    <ul><li>Airlie Beach</li><li>Bowen</li><li>Townsville</li></ul>
    <div class="hd">Contact</div>
    <ul><li style="font-size:10px">info@brightlinecoatings.com.au</li></ul>
    <a href="contact.html" style="display:block;background:#fff;color:var(--brand);text-align:center;font-size:10px;font-weight:600;height:30px;line-height:30px;margin-top:14px">Book Inspection</a>
    <div style="border-top:1px solid var(--deep-2);margin:40px -11px 0;padding-top:20px;text-align:center;font-size:9.5px;line-height:1.55;color:var(--brand-3)">© 2024 Brightline Coatings Co. Precision<br>Craftsmanship for the Coast.</div>
  </footer>
</section>

<!-- ========== EXPERTISE ========== -->
<section class="screen" style="left:609px;height:2880px">
  <header class="hdr"><a class="logo" href="index.html"><i></i>Brightline Coatings Co</a><a class="btn-dark sm" href="contact.html">Request Quote</a></header>
  <span class="a badge" style="left:11px;top:85px">OUR EXPERTISE</span>
  <h1 class="a" style="left:11px;top:116px;font-size:21px;line-height:1.3;width:236px">Precision Fabrication for Coastal Lifestyles</h1>
  <p class="a p" style="left:11px;top:186px;width:236px">From durable powder-coated fencing to architectural glass balustrades, we bring strength and style to the North Queensland coast.</p>
  <div class="a" style="left:0;top:283px;width:258px;height:1px;background:var(--line)"></div>

  <article class="a xcard" style="top:301px;height:353px">
    <div class="img" style="background:linear-gradient(180deg,#3f5a4e,#5b6a5a 40%,#7a6552 65%,#4a3f35)" role="img" aria-label="Deck walkway with engineered handrail"></div>
    <h3><svg viewBox="0 0 12 12" fill="none" stroke="#0054AA" stroke-width="1.3"><rect x="1" y="1" width="4" height="4"/><rect x="7" y="7" width="4" height="4"/><path d="M5 3h4v4M3 5v4h4"/></svg>Handrails</h3>
    <p class="p">Custom engineered handrails designed for safety and aesthetics. Our aluminum and steel solutions are built to withstand the humid Whitsunday climate while providing a sleek architectural finish.</p>
    <a class="more" href="handrails.html">Explore Details <svg viewBox="0 0 10 10" fill="none" stroke="currentColor"><path d="M1 5h8M6 2l3 3-3 3"/></svg></a>
  </article>
  <article class="a xcard" style="top:671px;height:353px">
    <div class="img" style="background:linear-gradient(180deg,#b9c8d6,#4d5560 40%,#2c2f36 70%,#6c7a88)" role="img" aria-label="Home with toughened glass balustrades"></div>
    <h3><svg viewBox="0 0 12 12" fill="none" stroke="#0054AA" stroke-width="1.3"><rect x="1" y="1" width="10" height="10"/><path d="M6 1v10M1 6h10"/></svg>Glass Balustrades</h3>
    <p class="p">Maintain your stunning views with our high-grade toughened glass balustrades. Features Marine-grade stainless steel fittings and custom spigots for a truly frameless look.</p>
    <a class="more" href="glass-balustrades.html">Explore Details <svg viewBox="0 0 10 10" fill="none" stroke="currentColor"><path d="M1 5h8M6 2l3 3-3 3"/></svg></a>
  </article>
  <article class="a xcard" style="top:1041px;height:353px">
    <div class="img" style="background:linear-gradient(180deg,#0a3466,#3d6a96 35%,#b9bcc0 55%,#d6d6d0 85%,#8f969a)" role="img" aria-label="Aluminium slat privacy screen and gate"></div>
    <h3><svg viewBox="0 0 12 12" fill="none" stroke="#0054AA" stroke-width="1.3"><rect x="1" y="1" width="10" height="10"/><path d="M1 4h10M1 6.5h10M1 9h10"/></svg>Privacy Screens</h3>
    <p class="p">High-quality aluminum slat screening that provides privacy without sacrificing airflow. Available in a wide range of powder-coated finishes to match your home's exterior palette.</p>
    <a class="more" href="privacy-screens.html">Explore Details <svg viewBox="0 0 10 10" fill="none" stroke="currentColor"><path d="M1 5h8M6 2l3 3-3 3"/></svg></a>
  </article>
  <article class="a xcard" style="top:1411px;height:354px">
    <div class="img" style="background:linear-gradient(180deg,#4a6760,#2d4540 45%,#7d8a90 70%,#3a3f48)" role="img" aria-label="Glass pool fencing with garden"></div>
    <h3><svg viewBox="0 0 12 12" fill="none" stroke="#0054AA" stroke-width="1.3"><path d="M3 1v7M7 1v7M3 3h4M3 5.5h4M1 9.5c1.5-1 2.5 1 4 0s2.5 1 4 0 1.5 0 2 0"/></svg>Pool Fencing</h3>
    <p class="p">Safety compliant pool fencing that looks as good as it functions. We offer both semi-frameless and fully frameless glass options, as well as modern flat-top aluminum designs.</p>
    <a class="more" href="pool-fencing.html">Explore Details <svg viewBox="0 0 10 10" fill="none" stroke="currentColor"><path d="M1 5h8M6 2l3 3-3 3"/></svg></a>
  </article>

  <div class="a standard" style="left:10px;top:1806px;width:236px;height:535px;padding:62px 16px 0">
    <svg width="36" height="36" viewBox="0 0 24 24"><path fill="#CADEEF" d="M12 1l2.6 2.2 3.4-.4.9 3.3 3 1.7-1.3 3.2 1.3 3.2-3 1.7-.9 3.3-3.4-.4L12 23l-2.6-2.2-3.4.4-.9-3.3-3-1.7L3.4 13 2.1 9.8l3-1.7.9-3.3 3.4.4z"/><path d="m8 12 3 3 5-6" stroke="#0054AA" stroke-width="2" fill="none"/></svg>
    <h2 style="margin-top:24px">The Brightline Standard of Precision</h2>
    <p style="font-size:11px;line-height:1.6;color:var(--brand-5);margin-top:26px">Every component is fabricated in our local facility, using industrial-grade materials specifically selected for the tropical conditions of the Whitsundays. Our powder coating process ensures a finish that resists corrosion and salt spray for decades.</p>
    <div class="checks" style="margin-top:32px">
      <span><svg viewBox="0 0 14 14" fill="none" stroke="#fff"><circle cx="7" cy="7" r="6"/><path d="m4.5 7 2 2 3-4"/></svg>Marine Grade Aluminum</span>
      <span><svg viewBox="0 0 14 14" fill="none" stroke="#fff"><circle cx="7" cy="7" r="6"/><path d="m4.5 7 2 2 3-4"/></svg>AS1288 Certified Glass</span>
      <span><svg viewBox="0 0 14 14" fill="none" stroke="#fff"><circle cx="7" cy="7" r="6"/><path d="m4.5 7 2 2 3-4"/></svg>Local Craftsmanship</span>
    </div>
  </div>

  <footer class="a foot" style="left:0;top:2372px;width:258px;height:508px;padding:36px 42px 0">
    <h2 style="line-height:1.3">Brightline Coatings Co</h2>
    <p class="t" style="margin-top:12px">© 2024 Brightline Coatings Co. Precision Craftsmanship for the Coast.</p>
    <div class="hd">Services</div>
    <ul><li class="dim"><a href="handrails.html">Handrails</a></li><li class="dim"><a href="privacy-screens.html">Privacy Screens</a></li><li class="dim"><a href="electric-gates.html">Electric Gates</a></li><li class="dim"><a href="pool-fencing.html">Pool Fencing</a></li><li class="dim"><a href="glass-balustrades.html">Glass Balustrades</a></li></ul>
    <div class="hd">Custom Work</div>
    <ul><li class="dim">Custom Fabrication</li><li class="dim">Airlie Beach Projects</li><li class="dim">Bowen Projects</li><li class="dim">Townsville Projects</li></ul>
    <div class="hd">Contact</div>
    <ul><li>Located in Cannonvale, QLD</li></ul>
    <a href="contact.html" style="display:inline-block;border:1px solid var(--brand-3);font-size:10px;padding:7px 14px;margin-top:4px">Email Us</a>
  </footer>
</section>

<!-- ========== CONTACT ========== -->
<section class="screen" style="left:887px;height:2139px">
  <header class="hdr"><a class="logo" href="index.html"><i></i>Brightline Coatings Co</a><a class="btn-dark sm" href="contact.html">Request Quote</a></header>
  <h1 class="a" style="left:11px;top:82px;font-size:21px;line-height:1.3;width:236px">Precision fabrication, on your terms.</h1>
  <p class="a p" style="left:11px;top:147px;width:236px">From architectural handrails to custom marine fabrication, our team delivers high-end aluminum and steel solutions across the North Queensland coast.</p>

  <div class="a box white" style="top:253px;height:562px;padding:20px 21px">
    <div class="label">Full Name</div><div class="field grey" style="height:37px">John Doe</div>
    <div class="label">Phone Number</div><div class="field grey" style="height:37px">0400 000 000</div>
    <div class="label" style="margin-top:22px">Service Type</div><div class="field grey" style="height:37px;color:var(--ink)">Select a service <svg width="8" height="5" viewBox="0 0 8 5" fill="none" stroke="#0054AA"><path d="m1 1 3 3 3-3"/></svg></div>
    <div class="label" style="margin-top:22px">Project Description</div><div class="field grey" style="height:102px;align-items:flex-start;padding-top:12px;line-height:1.55">Describe your project requirements, dimensions, and preferred materials...</div>
    <div class="label" style="margin-top:22px">Project Site Photo (Optional)</div>
    <div class="dash"><svg width="14" height="12" viewBox="0 0 14 12" fill="none" stroke="#0054AA"><rect x="1" y="3" width="12" height="8"/><path d="M4.5 3 5.5 1h3l1 2"/><circle cx="7" cy="7" r="2"/></svg>Tap to upload photos of the<br>installation area</div>
    <div class="btn-dark" style="text-align:center;margin-top:22px;height:36px;line-height:18px;font-size:9.5px">Submit Quote Request</div>
  </div>

  <div class="a box" style="top:831px;height:158px;padding:16px 16px">
    <svg class="icon" viewBox="0 0 16 16" fill="none" stroke="#0054AA" stroke-width="1.3"><path d="M3 2h2.5l1.2 3-1.6 1.2a7.5 7.5 0 0 0 4.7 4.7l1.2-1.6 3 1.2V13a1 1 0 0 1-1 1A11.5 11.5 0 0 1 2 3a1 1 0 0 1 1-1z"/><path d="M10 2a4 4 0 0 1 4 4M10 4.5A1.5 1.5 0 0 1 11.5 6"/></svg>
    <h3>Speak to our Team</h3>
    <p class="p" style="font-size:9.5px">For urgent inquiries or technical questions about our fabrication processes.</p>
    <div class="more" style="margin-top:12px">0400 000 000 <svg viewBox="0 0 10 10" fill="none" stroke="currentColor"><path d="M1 5h8M6 2l3 3-3 3"/></svg></div>
  </div>
  <div class="a box" style="top:1007px;height:140px;padding:16px 16px">
    <svg class="icon" viewBox="0 0 16 16" fill="none" stroke="#0054AA" stroke-width="1.3"><rect x="1.5" y="3" width="13" height="10"/><path d="m1.5 4 6.5 5 6.5-5"/></svg>
    <h3 style="margin-top:4px">Email Specifications</h3>
    <p class="p" style="font-size:9.5px">Send your project drawings or PDF specifications directly to our estimators.</p>
    <div class="more" style="margin-top:12px;font-size:9px">quotes@brightlinecoatings.com.au <svg viewBox="0 0 10 10" fill="none" stroke="currentColor"><path d="M1 5h8M6 2l3 3-3 3"/></svg></div>
  </div>
  <div class="a box" style="top:1165px;height:95px;padding:16px 16px">
    <div class="label" style="font-weight:600;color:var(--muted);margin-bottom:14px">Service Regions</div>
    <span class="chip">Airlie Beach</span><span class="chip">Bowen</span><span class="chip">Townsville</span><span class="chip">Whitsunday Islands</span>
  </div>

  <div class="a" style="left:10px;top:1292px;width:236px;height:264px;background:linear-gradient(160deg,#0a3466,#0054AA 40%,#0677BA 70%,#062a55);border-top:2px solid var(--line)" role="img" aria-label="Coastal service area map from Townsville to the Whitsunday hinterland"></div>
  <div class="a" style="left:25px;top:1462px;width:206px;height:124px;background:#fff;padding:14px 16px;box-shadow:0 4px 12px rgba(0,42,85,.25)">
    <h3 style="font-size:15px;font-weight:600">Coastal Service Zone</h3>
    <p class="p" style="font-size:9.5px;margin-top:8px">We service the entire corridor from Townsville down to the Whitsunday hinterland.</p>
    <div style="display:flex;align-items:center;gap:6px;font-size:9.5px;font-weight:700;color:var(--ink);margin-top:8px"><svg width="11" height="11" viewBox="0 0 12 12" fill="none" stroke="#0054AA"><path d="M6 11s4-3.6 4-6.5a4 4 0 0 0-8 0C2 7.4 6 11 6 11z"/><circle cx="6" cy="4.5" r="1.4"/></svg>Airlie Beach Headquarters</div>
  </div>

  <footer class="a foot" style="left:0;top:1604px;width:258px;height:535px;padding-top:34px">
    <h2>Brightline Coatings Co</h2>
    <p class="t" style="margin-top:12px">Precision craftsmanship for the coast. Specializing in architectural aluminum and marine-grade steel installations.</p>
    <div class="hd" style="margin-top:18px">Products</div>
    <ul><li><a href="handrails.html">Handrails</a></li><li><a href="privacy-screens.html">Privacy Screens</a></li><li><a href="electric-gates.html">Electric Gates</a></li><li><a href="pool-fencing.html">Pool Fencing</a></li><li><a href="glass-balustrades.html">Glass Balustrades</a></li></ul>
    <div class="hd" style="margin-top:12px">Locations</div>
    <ul><li>Airlie Beach</li><li>Bowen</li><li>Townsville</li></ul>
    <div class="hd" style="margin-top:12px">Connect</div>
    <div style="display:flex;gap:10px">
      <span style="width:26px;height:26px;border:1px solid var(--brand-2);display:flex;align-items:center;justify-content:center"><svg width="11" height="11" viewBox="0 0 12 12" fill="none" stroke="#fff"><circle cx="6" cy="6" r="4.5"/><path d="M1.5 6h9M6 1.5c-2 2.5-2 6.5 0 9M6 1.5c2 2.5 2 6.5 0 9"/></svg></span>
      <span style="width:26px;height:26px;border:1px solid var(--brand-2);display:flex;align-items:center;justify-content:center"><svg width="11" height="11" viewBox="0 0 12 12" fill="none" stroke="#fff"><rect x="1" y="3" width="10" height="7.5"/><path d="M4 3 5 1.5h2L8 3"/><circle cx="6" cy="6.7" r="1.8"/></svg></span>
    </div>
    <p style="font-size:8.5px;line-height:1.5;color:var(--brand-3);margin-top:40px">© 2024 Brightline Coatings Co. Precision Craftsmanship for the Coast.</p>
    <p style="font-size:8.5px;color:var(--brand-3);margin-top:2px;padding-left:42px">Privacy Policy&nbsp;&nbsp;&nbsp;&nbsp;&nbsp;Terms of Service</p>
  </footer>
</section>

</body>
</html>
```